Business Card Re-Design/Update

We'd like to update out business cards. I've included our current "Style guide" which has the colour scheme of the organisation in it. I've also included the branding files with logos etc in them.

I've also included a copy of one of our existing cards so that you can see how ugly/dated they look. I'd like a fresh modern corporate look.

Target Market(s)

These are for our clients, potential clients, industry contacts - like all business cards

Contact Information for Business Card

Name
Position
Company Address - Level 1, 47 Fernby Street, Carlow Qld 4072
Direct Phone
mobile
Email
Website -www.korvalit.com.au
Logo

Colors

Designer to choose colors to be used in the design.

Requirements
Must have
• Main Logo
• Cards will need to be editable to be able to personalize them for each new employee.
Nice to have
• The MapOut, ShipWell, KeepSteady would be okay to have if they can be sensibly and professionally added to the look without detracting from the main imagery.
• Maybe they could go on the back of the card? will leave this to your creative discretion as to whether/where they fit.
Should not have
• Should not have decorative or script fonts

```html
<!DOCTYPE html>
<html lang="en">
<head>
<meta charset="utf-8">
<title>korvalIT business card</title>
<link href="https://fonts.googleapis.com/css2?family=Arimo:wght@400;700&family=Questrial&display=swap" rel="stylesheet">
<style>
  :root {
    --bg: #e6e6e8;
    --paper: #ffffff;
    --red: #d71920;
    --charcoal: #3a3a3d;
    --ink: #2b2b2b;
    --magenta: #b0268f;
    --green: #6aa634;
    --blue: #2a8bc9;
  }
  * { margin: 0; padding: 0; box-sizing: border-box; }
  html, body { width: 1200px; height: 782px; overflow: hidden; background: var(--bg); }
  .stage { position: relative; width: 1200px; height: 782px; }
  .card {
    position: absolute; top: 236px; width: 540px; height: 309px;
    background: var(--paper); overflow: hidden;
    box-shadow: 0 8px 22px rgba(0,0,0,.18);
    font-family: "Arimo", Arial, sans-serif; color: var(--ink);
  }
  .card--front { left: 40px; }
  .card--back { left: 620px; }
  .card__shapes { position: absolute; inset: 0; }

  .person { position: absolute; left: 44px; top: 26px; }
  .person__name { color: var(--red); font-weight: 700; font-size: 15px; letter-spacing: .3px; }
  .person__role { font-size: 11.5px; margin-top: 2px; }

  .contacts { position: absolute; left: 26px; top: 118px; list-style: none; font-size: 12px; line-height: 17px; }
  .contacts li { display: flex; align-items: center; gap: 7px; }
  .contacts svg { width: 10px; height: 10px; fill: var(--red); flex: none; }

  .brand {
    position: absolute; left: 300px; top: 140px; display: flex; align-items: center; gap: 10px;
    font-family: "Questrial", Arial, sans-serif; font-size: 40px; color: var(--ink); letter-spacing: -.5px;
  }
  .brand__square { width: 14px; height: 14px; background: var(--red); }

  .address { position: absolute; right: 40px; top: 218px; text-align: right; font-size: 12.5px; line-height: 16px; }

  .back-brand {
    position: absolute; left: 40px; top: 108px; display: flex; align-items: center; gap: 12px;
    font-family: "Questrial", Arial, sans-serif; font-size: 54px; color: var(--paper);
  }
  .back-brand__square { width: 20px; height: 20px; background: var(--paper); }

  .services { position: absolute; right: 34px; top: 150px; list-style: none; text-align: right;
    font-family: "Questrial", Arial, sans-serif; font-size: 21px; line-height: 31px; }
  .services li { display: flex; justify-content: flex-end; align-items: center; gap: 8px; }
  .services span.dot { width: 12px; height: 12px; }
  .service--keep { color: var(--magenta); } .service--keep .dot { background: var(--magenta); }
  .service--map { color: var(--green); } .service--map .dot { background: var(--green); }
  .service--ship { color: var(--blue); } .service--ship .dot { background: var(--blue); }
</style>
</head>
<body>
<main class="stage">

  <section class="card card--front" aria-label="Card front">
    <svg class="card__shapes" viewBox="0 0 540 309" aria-hidden="true">
      <polygon points="0,14 34,14 22,40 0,40" fill="var(--charcoal)"/>
      <polygon points="20,14 40,14 28,40 14,40" fill="var(--red)"/>
      <polygon points="0,228 0,309 250,309 262,290 20,290" fill="var(--charcoal)"/>
      <polygon points="268,282 540,282 540,309 252,309" fill="var(--red)"/>
    </svg>

    <div class="person">
      <p class="person__name">MAREN HOLT</p>
      <p class="person__role">Business Development Manager</p>
    </div>

    <ul class="contacts">
      <li><svg viewBox="0 0 10 10"><path d="M2 0h2l1 3-1.5 1a6 6 0 0 0 2.5 2.5L7 5l3 1v2c0 1-1 2-2 2A8 8 0 0 1 0 2c0-1 1-2 2-2z"/></svg>+61 (0)412 555 019</li>
      <li><svg viewBox="0 0 10 10"><rect x="2" y="0" width="6" height="10" rx="1"/></svg>+61 (0)7 3555 0142</li>
      <li><svg viewBox="0 0 10 10"><rect x="0" y="3" width="10" height="5" rx="1"/><rect x="2" y="0" width="6" height="3"/></svg>+61 (0)7 3555 0148</li>
      <li><svg viewBox="0 0 10 10"><path d="M0 2h10v6H0z"/></svg>mholt@korvalit.com.au</li>
      <li><svg viewBox="0 0 10 10"><circle cx="5" cy="5" r="5"/></svg>www.korvalit.com.au</li>
    </ul>

    <div class="brand"><span class="brand__square"></span>korvalIT</div>

    <p class="address">Level 1, 47 Fernby Street<br>Carlow Qld 4072</p>
  </section>

  <section class="card card--back" aria-label="Card back">
    <svg class="card__shapes" viewBox="0 0 540 309" aria-hidden="true">
      <polygon points="0,0 150,0 60,309 0,309" fill="var(--charcoal)"/>
      <polygon points="20,70 300,70 268,210 0,210 0,90" fill="var(--red)"/>
    </svg>

    <div class="back-brand"><span class="back-brand__square"></span>korvalIT</div>

    <ul class="services">
      <li class="service--keep"><span class="dot"></span>KeepSteady</li>
      <li class="service--map"><span class="dot"></span>MapOut</li>
      <li class="service--ship"><span class="dot"></span>ShipWell</li>
    </ul>
  </section>

</main>
</body>
</html>
```